Google and facebook ads

Create four total ads, two for google and two for facebook for brightfinch.net.

The facebook ads will be a single image, and I will handle the text. Image should be consistent with this: https://notes.tidelark.io/banner-ad-specs. Image ratio is 1200x628 with an Image ratio of 1.91:1.

Target Market(s)

Parents who have young kids and are thinking about moving to a better school district.

Industry/Entity Type

Real Estate

Font styles to use
Sans Serif

Requirements
Must have
• Brightfinch logo.

```html
<!DOCTYPE html>
<html lang="en">
<head>
<meta charset="utf-8">
<title>Brightfinch – Top 30 Chicagoland Schools</title>
<link href="https://fonts.googleapis.com/css2?family=Nunito:wght@400;600;800;900&display=swap" rel="stylesheet">
<style>
  :root {
    --ink-brown: #3a2614;
    --halo-white: #ffffff;
    --wood-dark: #6b3f22;
    --wood-mid: #9a6337;
    --paper: #f3efe8;
    --crayon-teal: #6fb9c9;
    --crayon-red: #d2473c;
    --band-white: #ffffff;
    --caption-grey: #333333;
    --brand-navy: #1d3557;
    --brand-blue: #1f8fd6;
  }
  html, body {
    margin: 0;
    padding: 0;
    width: 1200px;
    height: 2400px;
    overflow: hidden;
    background: var(--band-white);
  }
  .ad {
    position: relative;
    width: 1200px;
    height: 2400px;
    overflow: hidden;
    font-family: "Nunito", sans-serif;
  }
  .ad__scene {
    position: absolute;
    left: 0;
    top: 0;
    width: 1200px;
    height: 2100px;
    background:
      radial-gradient(ellipse 700px 520px at 260px 300px, rgba(243,239,232,0.95), rgba(243,239,232,0) 70%),
      radial-gradient(ellipse 520px 620px at 380px 1750px, rgba(243,239,232,0.9), rgba(243,239,232,0) 70%),
      radial-gradient(ellipse 420px 380px at 980px 260px, rgba(210,71,60,0.35), rgba(210,71,60,0) 70%),
      radial-gradient(ellipse 360px 300px at 150px 220px, rgba(111,185,201,0.35), rgba(111,185,201,0) 70%),
      linear-gradient(160deg, var(--wood-mid) 0%, var(--wood-dark) 55%, var(--wood-mid) 100%);
  }
  .ad__headline {
    position: absolute;
    left: 0;
    top: 0;
    width: 1200px;
    margin: 0;
    text-align: center;
    color: var(--ink-brown);
    font-weight: 900;
    -webkit-text-stroke: 14px var(--halo-white);
    paint-order: stroke fill;
    line-height: 1;
  }
  .ad__headline span {
    position: absolute;
    left: 0;
    width: 1200px;
    display: block;
  }
  .headline__lead   { top: 140px;  font-size: 124px; }
  .headline__top    { top: 330px;  font-size: 215px; }
  .headline__region { top: 640px;  font-size: 178px; letter-spacing: 2px; }
  .headline__line   { font-size: 122px; font-weight: 800; }
  .headline__line--1 { top: 1030px; }
  .headline__line--2 { top: 1270px; }
  .headline__line--3 { top: 1510px; }
  .headline__line--4 { top: 1750px; }

  .ad__footer {
    position: absolute;
    left: 0;
    top: 2100px;
    width: 1200px;
    height: 300px;
    background: var(--band-white);
    text-align: center;
  }
  .footer__cta {
    position: absolute;
    top: 44px;
    left: 0;
    width: 1200px;
    margin: 0;
    font-size: 44px;
    font-weight: 600;
    color: var(--caption-grey);
  }
  .footer__brand {
    position: absolute;
    top: 130px;
    left: 0;
    width: 1200px;
    display: flex;
    justify-content: center;
    align-items: center;
    gap: 28px;
  }
  .brand__dot {
    width: 90px;
    height: 90px;
    border-radius: 50%;
    background: var(--brand-blue);
  }
  .brand__name {
    font-size: 104px;
    font-weight: 800;
    color: var(--brand-navy);
    line-height: 1;
  }
</style>
</head>
<body>
  <main class="ad">
    <div class="ad__scene" role="img" aria-label="Photo of a child's hands colouring holiday drawings with pencils on sheets of paper on a wooden table"></div>

    <h1 class="ad__headline">
      <span class="headline__lead">Find the</span>
      <span class="headline__top">Top 30</span>
      <span class="headline__region">Chicagoland</span>
      <span class="headline__line headline__line--1">Schools with</span>
      <span class="headline__line headline__line--2">Homes for Sale</span>
      <span class="headline__line headline__line--3">that Match Your</span>
      <span class="headline__line headline__line--4">Requirements</span>
    </h1>

    <footer class="ad__footer">
      <p class="footer__cta">To Learn More Visit</p>
      <div class="footer__brand">
        <div class="brand__dot"></div>
        <div class="brand__name">Brightfinch.net</div>
      </div>
    </footer>
  </main>
</body>
</html>
```